Manufacturer of prepared Persian ready meals needs a product concept design

I need a product concept design for a new company based in the UK called 'Valdren Kitchen Ltd'.
The winner will potentially be selected to produce prototype designs for our other products.
For this project, the product will be called "Ghormeh Sabzi". This needs to be on the design to let consumers know what it is.
Whilst still in the concept stage, the aim of the company is to produce refrigerated microwaveable / oven Persian ready meal for retail supermarket consumers, and may also have an online platform for direct to consumer sales.
I have provided quite a few competitor examples of products.
I would like the product in a black or clear round bowl. It will be split into two sections (Half stew / Half rice) by the sleeve, which you are designing. I would like the food to be visible on either side of the label, so the consumer knows what they are eating.
The logo is provided within the file attachments and needs to be on prominent display on the pouch.
The mission for Valdren Kitchen Ltd brand is:
"Bringing 2,500 years of scented history to your table".
This needs to be present on the sleeve.
The product needs to represent the ethnicity of the brand throughout the design, and the same font to be used throughout.
Persian architecture was filled with a wide range of vibrant colours and has been engineered to stand the test of time, so I would like that to be incorporated into the product design (see attached examples of Persian geometry).
Alternatively Persian carpets are world renowned for their quality, so examples of this could be displayed on the packaging.
These will have to be artistically interpreted to avoid potential copyright; I am looking for individual artistic design.
It needs to represent a super quality, royalty & decadence throughout, and stand out on the shelves to the consumer above all the other competitor products.
To comply with food standards, the sleeve must have a nutritional label on display. I have attached a generic example for you to use. You may create your own representation of it.
Ghormeh Sabzi is a natural source of fibre, high in protein, gluten and dairy free, so I would like this displayed on the sleeve, as well as the the words:
- Traditionally rich in aromatic herbs, tender slow cooked lamb, red kidney beans & dried limes
- One of the oldest dishes in Persian history
You can find pictures of the food provided in the files. Note, these are not my pictures, but give you an idea of what will be provided inside.
Some designers have uploaded the same design up to 5 times, others twice. Only 18 have been uploaded, but it says 20, so I think 2 have been removed?

```html
<!DOCTYPE html>
<html lang="en">
<head>
<meta charset="utf-8">
<title>Valdren Kitchen – Ghormeh Sabzi sleeve concepts</title>
<link rel="stylesheet" href="https://fonts.googleapis.com/css2?family=Jost:ital,wght@0,300;0,400;0,500;0,600;1,300;1,400&display=swap">
<style>
  :root {
    --page: #ffffff;
    --herb-ground: #353806;
    --herb-arch: #3e5e3f;
    --herb-lattice: #415224;
    --herb-line: #4d6d44;
    --garnet-ground: #5c2835;
    --garnet-arch: #7e0006;
    --garnet-lattice: #751a28;
    --garnet-line: #8f0b1a;
    --saffron: #fff35c;
    --ivory: #ffffff;
    --energy: #dcae8c;
    --fat: #b5c48f;
    --sugars: #a9cd47;
    --salt: #f58d4b;
    --saturates: #ef3b5e;
    --ink: #2a2a2a;
  }
  * { box-sizing: border-box; margin: 0; padding: 0; }
  html, body { width: 837px; height: 1200px; overflow: hidden; background: var(--page); }
  body { font-family: "Jost", sans-serif; position: relative; }

  .sleeve { position: absolute; top: 0; width: 414px; height: 1200px; overflow: hidden; background: var(--ground); }
  .sleeve--herb { left: 0; --ground: var(--herb-ground); --arch: var(--herb-arch); --lattice: var(--herb-lattice); --line: var(--herb-line); }
  .sleeve--garnet { left: 423px; --ground: var(--garnet-ground); --arch: var(--garnet-arch); --lattice: var(--garnet-lattice); --line: var(--garnet-line); }

  .sleeve__border { position: absolute; left: 11px; top: 126px; width: 392px; height: 956px;
    border: 16px solid var(--lattice); }
  .sleeve__panel { position: absolute; left: 27px; top: 144px; width: 360px; height: 922px;
    border: 1px solid var(--line); }

  .arch { position: absolute; left: 27px; width: 360px; height: 170px; display: block; }
  .arch__shape { fill: var(--arch); }
  .arch--top { top: 144px; }
  .arch--bottom { top: 896px; transform: scaleY(-1); }

  .centered { position: absolute; left: 0; width: 414px; text-align: center; }

  .brand { top: 282px; display: flex; flex-direction: column; align-items: center; }
  .brand__mark { width: 110px; height: 110px; border: 5px solid var(--ivory); }
  .brand__name { margin-top: 14px; color: var(--ivory); font-weight: 500; font-size: 30px; letter-spacing: 9px; line-height: 1; padding-left: 9px; }
  .brand__sub { margin-top: 10px; color: var(--ivory); font-weight: 500; font-size: 16px; letter-spacing: 8px; line-height: 1; padding-left: 8px; }

  .mission { top: 496px; color: var(--saffron); font-style: italic; font-weight: 300; font-size: 15px; line-height: 21px; }
  .product-name { top: 556px; color: var(--saffron); font-weight: 400; font-size: 57px; line-height: 61px; letter-spacing: -0.5px; }
  .weight { top: 697px; color: var(--ivory); font-style: italic; font-weight: 400; font-size: 23px; }
  .weight small { font-size: 12px; }
  .description { top: 753px; color: var(--ivory); font-style: italic; font-weight: 300; font-size: 12.5px; line-height: 16px; }
  .heritage { top: 798px; color: var(--saffron); font-style: italic; font-weight: 300; font-size: 12.5px; }

  .nutrition { top: 838px; }
  .nutrition__title { color: var(--ivory); font-weight: 600; font-size: 10px; }
  .nutrition__chips { display: flex; justify-content: center; margin-top: 3px; }
  .chip { width: 40.5px; height: 55px; border-radius: 18px 18px 0 0; color: var(--ink);
    display: flex; flex-direction: column; align-items: center; padding-top: 6px; font-size: 8.5px; line-height: 1.05; }
  .chip__label { font-weight: 600; font-size: 8px; }
  .chip__value { font-weight: 300; font-size: 9px; margin-top: 3px; }
  .chip__value--small { font-size: 7px; margin-top: 3px; }
  .chip__level { margin-top: 2px; background: var(--ivory); border-radius: 3px; padding: 0 5px; font-weight: 600; font-size: 6.5px; line-height: 9px; }
  .chip__pct { margin-top: auto; margin-bottom: 2px; font-weight: 600; font-size: 6.5px; }
  .chip--energy { background: var(--energy); }
  .chip--fat { background: var(--fat); }
  .chip--sugars { background: var(--sugars); }
  .chip--salt { background: var(--salt); }
  .chip--saturates { background: var(--saturates); }
  .nutrition__note { margin-top: 5px; color: var(--ivory); font-style: italic; font-weight: 300; font-size: 6px; line-height: 8.5px; }

  .sleeve--garnet .mission { top: 487px; }
  .sleeve--garnet .product-name { top: 544px; }
  .sleeve--garnet .weight { top: 686px; }
  .sleeve--garnet .description { top: 747px; }
  .sleeve--garnet .heritage { top: 794px; }
  .sleeve--garnet .nutrition { top: 836px; }
</style>
</head>
<body>

<section class="sleeve sleeve--herb">
  <div class="sleeve__border" role="img" aria-label="Persian diamond-lattice border pattern"></div>
  <div class="sleeve__panel"></div>
  <svg class="arch arch--top" viewBox="0 0 688 325" preserveAspectRatio="none" role="img" aria-label="Persian floral arabesque corner ornaments framing an arch"><path class="arch__shape" d="M0 0 H688 V325 C640 320 600 300 585 240 C570 150 430 120 400 60 C380 30 350 15 344 0 C338 15 308 30 288 60 C258 120 118 150 103 240 C88 300 48 320 0 325 Z"/></svg>
  <svg class="arch arch--bottom" viewBox="0 0 688 325" preserveAspectRatio="none" role="img" aria-label="Persian floral arabesque corner ornaments framing an arch"><path class="arch__shape" d="M0 0 H688 V325 C640 320 600 300 585 240 C570 150 430 120 400 60 C380 30 350 15 344 0 C338 15 308 30 288 60 C258 120 118 150 103 240 C88 300 48 320 0 325 Z"/></svg>

  <div class="centered brand">
    <div class="brand__mark"></div>
    <p class="brand__name">VALDREN</p>
    <p class="brand__sub">KITCHEN</p>
  </div>
  <p class="centered mission">Bringing 2,500 years of<br>scented history to your table</p>
  <h1 class="centered product-name">GHORMEH<br>SABZI</h1>
  <p class="centered weight">400<small>g</small></p>
  <p class="centered description">Traditionally rich in aromatic herbs, Tender slow cooked lamb,<br>Red kidney beans &amp; dried limes.</p>
  <p class="centered heritage">One of the oldest dishes in Persian history.</p>
  <div class="centered nutrition">
    <p class="nutrition__title">Each serving (150g) contains</p>
    <div class="nutrition__chips">
      <div class="chip chip--energy"><span class="chip__label">Energy</span><span class="chip__value chip__value--small">1046kJ<br>250kcal</span><span class="chip__pct">13%</span></div>
      <div class="chip chip--fat"><span class="chip__label">Fat</span><span class="chip__value">3.0g</span><span class="chip__level">LOW</span><span class="chip__pct">4%</span></div>
      <div class="chip chip--sugars"><span class="chip__label">Sugars</span><span class="chip__value">34g</span><span class="chip__level">LOW</span><span class="chip__pct">38%</span></div>
      <div class="chip chip--salt"><span class="chip__label">Salt</span><span class="chip__value">0.9g</span><span class="chip__level">HIGH</span><span class="chip__pct">15%</span></div>
      <div class="chip chip--saturates"><span class="chip__label">Saturates</span><span class="chip__value">1.3g</span><span class="chip__level">MED</span><span class="chip__pct">7%</span></div>
    </div>
    <p class="nutrition__note">of an adult's reference intake<br>Typical values (as sold) per 100g: 697kJ/ 167kcal</p>
  </div>
</section>

<section class="sleeve sleeve--garnet">
  <div class="sleeve__border" role="img" aria-label="Persian diamond-lattice border pattern"></div>
  <div class="sleeve__panel"></div>
  <svg class="arch arch--top" viewBox="0 0 688 325" preserveAspectRatio="none" role="img" aria-label="Persian floral arabesque corner ornaments framing an arch"><path class="arch__shape" d="M0 0 H688 V325 C640 320 600 300 585 240 C570 150 430 120 400 60 C380 30 350 15 344 0 C338 15 308 30 288 60 C258 120 118 150 103 240 C88 300 48 320 0 325 Z"/></svg>
  <svg class="arch arch--bottom" viewBox="0 0 688 325" preserveAspectRatio="none" role="img" aria-label="Persian floral arabesque corner ornaments framing an arch"><path class="arch__shape" d="M0 0 H688 V325 C640 320 600 300 585 240 C570 150 430 120 400 60 C380 30 350 15 344 0 C338 15 308 30 288 60 C258 120 118 150 103 240 C88 300 48 320 0 325 Z"/></svg>

  <div class="centered brand">
    <div class="brand__mark"></div>
    <p class="brand__name">VALDREN</p>
    <p class="brand__sub">KITCHEN</p>
  </div>
  <p class="centered mission">Bringing 2,500 years of<br>scented history to your table</p>
  <h1 class="centered product-name">GHORMEH<br>SABZI</h1>
  <p class="centered weight">400<small>g</small></p>
  <p class="centered description">Traditionally rich in aromatic herbs, Tender slow cooked lamb,<br>Red kidney beans &amp; dried limes.</p>
  <p class="centered heritage">One of the oldest dishes in Persian history.</p>
  <div class="centered nutrition">
    <p class="nutrition__title">Each serving (150g) contains</p>
    <div class="nutrition__chips">
      <div class="chip chip--energy"><span class="chip__label">Energy</span><span class="chip__value chip__value--small">1046kJ<br>250kcal</span><span class="chip__pct">13%</span></div>
      <div class="chip chip--fat"><span class="chip__label">Fat</span><span class="chip__value">3.0g</span><span class="chip__level">LOW</span><span class="chip__pct">4%</span></div>
      <div class="chip chip--sugars"><span class="chip__label">Sugars</span><span class="chip__value">34g</span><span class="chip__level">LOW</span><span class="chip__pct">38%</span></div>
      <div class="chip chip--salt"><span class="chip__label">Salt</span><span class="chip__value">0.9g</span><span class="chip__level">HIGH</span><span class="chip__pct">15%</span></div>
      <div class="chip chip--saturates"><span class="chip__label">Saturates</span><span class="chip__value">1.3g</span><span class="chip__level">MED</span><span class="chip__pct">7%</span></div>
    </div>
    <p class="nutrition__note">of an adult's reference intake<br>Typical values (as sold) per 100g: 697kJ/ 167kcal</p>
  </div>
</section>

</body>
</html>
```